Community coffee table book/quiz book

I need a couple of things for my book:
- Book cover (Title: "1000 spørsmål om Kvernhaugen")
- "Cover pages" for each chapter of the book (15-16 chapters)
- "Watermark" or background design for all the pages of the book.
- A cover image for the book's Kretsbok page.
- Design of a paper "belt"

The book:
The book will consist of about 200+ pages with ten questions on one page and ten answers on the next.

The name of the book is "1000 spørsmål om Kvernhaugen" which means 1000 questions about Fyllingsdalen (Fyllingsdalen is a suburb of the city Bergen in Norway). Author is Helge Myrvold.
The questions in the book are grouped in chapters like:
History
Facts
Schools
Businesses
People/profiles
Sport
Culture
Buildings/Landmarks/Sculptures
The different areas of the suburb
The city
Language/expressions
Nature
The names of the chapters are not set, so it would be good to have the option to change the title of the pages without having to contact the designer (maybe by adding the text on top of the cover page?). I therefore suggest that these images are without text.
The book size is 18X18 cm.

The chapter cover pages:
The book will basically consist of text. Ten questions on one page, and ten questions on the next. Visually it will be quite "boring" to look at. I would therefore like to have a chapter cover page for each chapter, preferable in colour.

Water mark:
To avoid having a book full of white pages with limited amount of text I thought of having some kind of design on each page. I do not know how this should be done, but maybe it is possible to create some kind of background image or watermark image with similar design as the book cover and the chapter covers?

The Kretsbok cover image:
This should be the same as, or similar to, the book cover.
I believe the optimal size is 828px x 315px?

Paper "belt":
The book is to be sold for charity. The receiver of the money is the local sports club. I would like to have the book "wrapped in a 5-6 cm wide paper belt with the logo of the sports club (please see logo and colours here: http://www.ilbrattlia.no). I do not think that the book cover itself should have the sports club's color (purple), but maybe the paper band could? (Again: YOU are the designer)

Photos:
I reckon you would like some photos for both the book cover and the chapter covers. I will of course do the best I can to provide these photos when I have selected a designer. I the meantime

Target Market(s)

Target market is middle clas men and women 35+ from the geographical area Fyllingsdalen.

Industry/Entity Type

Community

Font styles to use
Serif
Sans Serif

Requirements
Must have
• The book will be sold by children on doors. The buyers will probably take a look briefly through the book and then decide if they are going to buy.
• It is important that they like the question types, categories and some of the actual questions they read. But it is also important that they like the look of the book. Therefore the book cover and the chapter cover pages must be appealing enough for the buyers to want this book on theor coffee table.
Nice to have
• I have uploaded a short video clip to Vidtrekk (https://www.vidtrekk.example/watch?v=qx7Ta2Lm9pz). This a promo clip from Pimlo Kanalen. I felt inspired when I saw it and thought that backgrounds like the ones used in the promo could also be used as backgrounds for each chapter's cover pages. Maybe different colour for each chapter? Screenshots from the clip is uploaded below.
• Then again: Maybe I am an idiot? YOU are the designer :-)
Should not have
• There has been some rivalry between two sportsclubs in the region after the clubs was merged a couple of years ago. I therefore believe we should therefore try avoid both the old clubs' colours (blue&yellow and green) and the new club's colour (purple).

```html
<!DOCTYPE html>
<html lang="no">
<head>
<meta charset="utf-8">
<title>1000 spørsmål om Kvernhaugen – bokomslag</title>
<link rel="stylesheet" href="https://fonts.googleapis.com/css2?family=Quicksand:wght@400&family=Oswald:wght@400;500&family=Kaushan+Script&family=Nunito:wght@800&display=swap">
<style>
  :root {
    --page-bg: #ffffff;
    --gold: #c9a010;
    --gold-edge: #d8b21a;
    --board: #2f2d2a;
    --board-light: #3a3835;
    --pink: #f4c3cc;
    --peach: #e9c9b8;
    --script-gold: #f2be1a;
    --white: #ffffff;
    --ink: #111111;
  }
  html, body {
    margin: 0;
    width: 1200px;
    height: 1000px;
    overflow: hidden;
    background: var(--page-bg);
  }
  .canvas {
    position: relative;
    width: 1200px;
    height: 1000px;
  }
  .cover-art {
    position: absolute;
    left: 0;
    top: 0;
  }
  .title-number {
    font-family: "Quicksand", sans-serif;
    font-weight: 400;
    font-size: 190px;
    fill: none;
    stroke: var(--pink);
    stroke-width: 2.4;
  }
  .title-word {
    font-family: "Oswald", sans-serif;
    font-weight: 500;
    font-size: 94px;
    fill: none;
    stroke: var(--peach);
    stroke-width: 1.4;
  }
  .title-place {
    font-family: "Kaushan Script", cursive;
    fill: var(--script-gold);
  }
  .title-place--small { font-size: 40px; }
  .title-place--large { font-size: 74px; }
  .author {
    font-family: "Nunito", sans-serif;
    font-weight: 800;
    font-size: 17px;
    fill: var(--white);
  }
  .caption {
    position: absolute;
    left: 0;
    width: 1200px;
    top: 872px;
    margin: 0;
    text-align: center;
    font-family: "Oswald", sans-serif;
    font-weight: 400;
    font-size: 42px;
    color: var(--ink);
    letter-spacing: 0.5px;
  }
</style>
</head>
<body>
<main class="canvas">
  <svg class="cover-art" width="1200" height="1000" viewBox="0 0 1200 1000" xmlns="http://www.w3.org/2000/svg">
    <defs>
      <radialGradient id="board-texture" cx="0.55" cy="0.45" r="0.7">
        <stop offset="0" stop-color="#3a3835"/>
        <stop offset="1" stop-color="#2f2d2a"/>
      </radialGradient>
      <linearGradient id="skyline-fade" x1="0" y1="0" x2="0" y2="1">
        <stop offset="0" stop-color="#35332f" stop-opacity="0"/>
        <stop offset="1" stop-color="#35332f" stop-opacity="0.8"/>
      </linearGradient>
      <clipPath id="board-clip">
        <path d="M245,212 Q560,40 1012,125 L1012,705 Q690,860 245,790 Z"/>
      </clipPath>
    </defs>

    <rect class="cover-frame" x="245" y="73" width="767" height="767" fill="var(--gold)" stroke="var(--gold-edge)" stroke-width="1"/>

    <path class="chalkboard" d="M245,212 Q560,40 1012,125 L1012,705 Q690,860 245,790 Z" fill="url(#board-texture)"/>

    <g clip-path="url(#board-clip)">
      <rect class="town-silhouette" role="img" aria-label="Svak silhuett av bydelen" x="245" y="600" width="767" height="200" fill="url(#skyline-fade)"/>
    </g>

    <text class="title-number" x="475" y="358" textLength="275" lengthAdjust="spacingAndGlyphs">1000</text>

    <g class="dot-row" fill="var(--white)">
      <circle cx="476" cy="384" r="4"/><circle cx="500.5" cy="384" r="4"/><circle cx="525" cy="384" r="4"/>
      <circle cx="549.5" cy="384" r="4"/><circle cx="574" cy="384" r="4"/><circle cx="598.5" cy="384" r="4"/>
      <circle cx="623" cy="384" r="4"/><circle cx="647.5" cy="384" r="4"/><circle cx="672" cy="384" r="4"/>
      <circle cx="696.5" cy="384" r="4"/><circle cx="721" cy="384" r="4"/><circle cx="745" cy="384" r="4"/>
    </g>

    <text class="title-word" x="383" y="494" textLength="482" lengthAdjust="spacingAndGlyphs">SPØRSMÅL</text>

    <rect class="divider-ornament" role="img" aria-label="Dekorativ skillelinje" x="410" y="515" width="422" height="4" rx="2" fill="var(--white)" opacity="0.85"/>

    <text class="title-place title-place--small" x="627" y="560" text-anchor="middle">om</text>
    <text class="title-place title-place--large" x="637" y="620" text-anchor="middle" textLength="390" lengthAdjust="spacingAndGlyphs">Kvernhaugen</text>

    <text class="author" x="634" y="690" text-anchor="middle">Helge Myrvold</text>
  </svg>

  <p class="caption">BOOK COVER</p>
</main>
</body>
</html>
```